Bramwell's Meadow Larder Limited (Uncoded design only)

To design a new modern website to replace an existing website.
www.clothdumplings.co.uk
we want to keep the same website address and pages - unless you hae new ideas for the pages.
We are initially looking for design only (no coding requirements)
We want wording 'Bramwell's Cloth Dumplings' to be used and Bramwell's Meadow Larder Limited to be the comapny address rather than what it is now.
I attach a new logo 'Bramwell lad' and new packaing design (Zip file). NOTE the blue man is to be replaced with the new 'Bramwells lad 'file i.e.the man with the union jack flag on his chest.
We would like coordination of the packing colourson the new website please.

Target Market(s)

Online sales to supermarkets

Industry/Entity Type

Food manufacturing

Coding

Coded - Design and coding required

Number of Pages Required

4 page

Font styles to use
Other font styles liked:
• Happy for any choice of font styles as I'm not stuck with the font of the packaging. I'm happy to go with what you feel looks the best and we can change the package to suit

Requirements
Must have
• Links to Facebook, Instagram and LinkedIn

```html
<!DOCTYPE html>
<html lang="en">
<head>
<meta charset="utf-8">
<title>Bramwell's Cloth Dumplings</title>
<link rel="stylesheet" href="https://fonts.googleapis.com/css2?family=Federo&family=Questrial&family=Kaushan+Script&display=swap">
<style>
:root{
  --blue:#2a4a9f;
  --blue-deep:#223f8c;
  --orange:#eb7b3b;
  --cream:#fbfaf6;
  --white:#ffffff;
  --line:#9aa6c9;
  --head:'Federo',sans-serif;
  --body:'Questrial',sans-serif;
  --script:'Kaushan Script',cursive;
}
*{margin:0;padding:0;box-sizing:border-box}
html,body{width:1200px;height:4843px;overflow:hidden;background:var(--cream)}
body{font-family:var(--body);color:var(--blue)}
.page{position:relative;width:1200px;height:4843px;overflow:hidden}
.backdrop{position:absolute;left:0;top:0}
.abs{position:absolute}
.btn{position:absolute;display:flex;align-items:center;justify-content:center;background:var(--orange);color:var(--white);border-radius:24px;font-family:var(--body);font-weight:700;letter-spacing:1px;text-decoration:none;box-shadow:0 3px 6px rgba(0,0,0,.15)}
.brand{left:60px;top:34px;display:flex;align-items:center;gap:12px;color:var(--white);font-size:21px;line-height:25px;width:240px}
.brand-dot{width:30px;height:30px;border-radius:50%;background:var(--white);flex:none}
.nav a{position:absolute;top:30px;color:var(--white);font-family:var(--body);font-size:22px;letter-spacing:1.5px;text-decoration:none}
.nav .shop-pill{top:26px;left:980px;width:98px;height:38px;font-size:22px}
.basket{left:1128px;top:26px}
.hero-title{left:75px;top:174px;font-family:var(--head);font-size:50px;line-height:58px;color:var(--white);letter-spacing:3px;font-weight:400}
.hero-tag{left:75px;top:318px;font-family:var(--script);font-size:40px;color:var(--white)}
.photo{position:absolute}
.section-title{position:absolute;left:0;width:1200px;text-align:center;font-family:var(--head);font-weight:400;letter-spacing:3px}
.lead{position:absolute;text-align:center;font-size:30px;line-height:45px;letter-spacing:1.2px}
.delivery-title{left:51px;top:796px;font-family:var(--head);font-weight:400;font-size:30px;line-height:47px;letter-spacing:1.5px}
.delivery-copy{left:51px;top:906px;width:680px;font-size:21px;line-height:35px;letter-spacing:1px}
.delivery-copy p+p{margin-top:35px}
.cook{position:absolute;top:1562px;width:180px;text-align:center;color:var(--white);font-size:22px;letter-spacing:1px}
.cook svg{display:block;margin:0 auto 14px}
.dish{position:absolute;top:1698px;width:184px;height:182px;border-radius:10px}
.sweet-copy{left:52px;top:2462px;width:370px;color:var(--white);font-size:30px;line-height:45px;font-weight:700;letter-spacing:1.2px}
.apple-title{left:50px;top:2876px;font-family:var(--head);font-weight:400;font-size:52px;line-height:66px;letter-spacing:3px;color:var(--blue)}
.factory{position:absolute;top:3502px;height:185px;border-radius:6px}
.contact-form{position:absolute;left:237px;top:3992px;width:726px}
.contact-form label{display:block;font-size:22px;height:22px;line-height:22px;letter-spacing:1px}
.field{display:block;width:726px;height:37px;border:1.5px solid var(--line);background:var(--white);margin-bottom:17px}
.field.tall{height:90px}
.contact-form .spam{font-size:15px}
.footer-col{position:absolute;top:4636px;color:var(--white)}
.footer-col h4{font-family:var(--body);font-weight:400;font-size:23px;letter-spacing:2px;margin-bottom:16px}
.footer-col p,.footer-col a{display:block;font-size:15px;letter-spacing:1px;color:var(--white);text-decoration:none;line-height:31px}
.social{display:flex;gap:22px;margin-top:4px}
.social span{width:26px;height:26px;border-radius:50%;background:var(--white)}
.rule{position:absolute;left:49px;top:4774px;width:1106px;height:1px;background:var(--white)}
.copyright{position:absolute;left:49px;top:4788px;font-size:14px;color:var(--white);letter-spacing:.5px}
</style>
</head>
<body>
<div class="page">

<svg class="backdrop" width="1200" height="4843" viewBox="0 0 1200 4843" aria-hidden="true">
  <defs>
    <filter id="lift" x="-10%" y="-10%" width="120%" height="130%"><feDropShadow dx="0" dy="6" stdDeviation="6" flood-opacity=".22"/></filter>
  </defs>
  <rect x="0" y="300" width="1200" height="700" fill="var(--orange)"/>
  <path d="M0,720 C260,735 560,795 790,792 C960,790 1060,730 1200,720 V1330 H0 Z" fill="var(--cream)" filter="url(#lift)"/>
  <path d="M0,0 H1200 V330 C1060,360 980,385 870,405 C700,432 600,415 450,440 C300,468 150,490 0,472 Z" fill="var(--blue)" filter="url(#lift)"/>
  <path d="M0,1328 C320,1330 560,1300 710,1205 C850,1115 1010,1135 1200,1120 V1970 H0 Z" fill="var(--blue)"/>
  <path d="M0,2262 C300,2260 520,2262 700,2292 C880,2322 1040,2345 1200,2372 V3100 H0 Z" fill="var(--orange)"/>
  <path d="M0,2892 C80,2785 200,2762 330,2722 C450,2682 470,2522 560,2482 C700,2422 900,2440 1200,2420 V3200 H0 Z" fill="var(--cream)" filter="url(#lift)"/>
  <path d="M0,3295 C300,3290 500,3250 700,3180 C900,3110 1050,3062 1200,3045 V3762 H0 Z" fill="var(--blue)"/>
  <rect x="0" y="4600" width="1200" height="243" fill="var(--blue)"/>
  <path d="M78,302 C220,292 360,288 490,296" stroke="var(--orange)" stroke-width="4" fill="none" stroke-linecap="round"/>
</svg>

<header>
  <div class="abs brand"><span class="brand-dot"></span><span>Bramwell's Meadow Larder</span></div>
  <nav class="nav">
    <a href="#" style="left:442px">HOME</a>
    <a href="#" style="left:596px">DELIVERY</a>
    <a href="#" style="left:800px">CONTACT</a>
    <a href="#" class="btn shop-pill">SHOP</a>
  </nav>
  <svg class="abs basket" width="46" height="40" viewBox="0 0 46 40" aria-label="Basket">
    <path d="M4,14 H38 L33,34 H9 Z" fill="none" stroke="#fff" stroke-width="3.5" stroke-linejoin="round"/>
    <path d="M12,14 L20,4 M30,14 L22,4" stroke="#fff" stroke-width="3" stroke-linecap="round"/>
    <path d="M15,19 V29 M21,19 V29 M27,19 V29" stroke="#fff" stroke-width="2.5"/>
    <circle cx="38" cy="8" r="8" fill="var(--orange)"/>
    <text x="38" y="12" font-size="11" fill="#fff" text-anchor="middle" font-family="Questrial,sans-serif">1</text>
  </svg>
</header>

<section class="hero">
  <h1 class="abs hero-title">HANDMADE IN<br>LANCASHIRE</h1>
  <p class="abs hero-tag">A taste of the North</p>
  <a href="#" class="btn" style="left:75px;top:406px;width:320px;height:47px;font-size:22px">DISCOVER OUR DISHES</a>
  <svg class="photo" style="left:658px;top:170px" width="452" height="290" viewBox="0 0 452 290" role="img" aria-label="Plated cloth dumpling with chips, mushy peas and a jug of gravy">
    <defs><radialGradient id="plate" cx="50%" cy="50%" r="60%"><stop offset="0" stop-color="#d9a760"/><stop offset=".55" stop-color="#c99a5a"/><stop offset=".72" stop-color="#f3f1ec"/><stop offset="1" stop-color="#dcdad4"/></radialGradient></defs>
    <ellipse cx="226" cy="160" rx="222" ry="125" fill="url(#plate)"/>
  </svg>
</section>

<section class="greatest">
  <h2 class="section-title" style="top:538px;font-size:52px;color:var(--white)">ONLY THE GREATEST</h2>
  <p class="lead" style="left:160px;top:619px;width:880px;color:var(--white)">Our rag puddings are made from suet pastry and the very best cuts of beefsteak without the use of any preservatives.</p>
</section>

<section class="delivery">
  <h3 class="abs delivery-title">LOCAL DELIVERY ONLY £1<br>IN ALL ‘OL’ POSTCODES</h3>
  <div class="abs delivery-copy">
    <p>You can get our puddings &amp; pies brought straight to your doorstep. Delivery charge will be applied automatically when you proceed to checkout as local postcode is recognised.</p>
    <p>If you prefer, you’re welcome to come and<br>collect your order from our factory shop!</p>
  </div>
  <a href="#" class="btn" style="left:51px;top:1240px;width:209px;height:45px;font-size:22px">SHOP ONLINE</a>
  <svg class="photo" style="left:658px;top:790px" width="490" height="460" viewBox="0 0 490 460" role="img" aria-label="Open delivery box of wrapped cloth dumplings with its printed lid">
    <defs><linearGradient id="box" x1="0" y1="0" x2="1" y2="1"><stop offset="0" stop-color="#c9ad7f"/><stop offset=".5" stop-color="#f1ede4"/><stop offset="1" stop-color="#e6e3dc"/></linearGradient></defs>
    <path d="M240,0 L490,60 L470,310 L380,330 L300,380 L40,460 L0,360 L110,250 L150,90 Z" fill="url(#box)"/>
  </svg>
</section>

<section class="cooking">
  <h2 class="section-title" style="top:1388px;font-size:44px;color:var(--white)">HOW DO YOU LIKE YOURS?</h2>
  <p class="lead" style="left:0;top:1472px;width:1200px;color:var(--white)">Our puddings can be cooked in different ways</p>
  <div class="cook" style="left:188px">
    <svg width="64" height="64" viewBox="0 0 64 64" aria-hidden="true"><rect x="4" y="4" width="56" height="56" rx="3" fill="none" stroke="#fff" stroke-width="3"/><line x1="4" y1="16" x2="60" y2="16" stroke="#fff" stroke-width="3"/><rect x="12" y="24" width="40" height="28" fill="none" stroke="#fff" stroke-width="3"/><circle cx="24" cy="10" r="2" fill="#fff"/><circle cx="32" cy="10" r="2" fill="#fff"/><circle cx="40" cy="10" r="2" fill="#fff"/></svg>
    oven bake
  </div>
  <div class="cook" style="left:403px">
    <svg width="64" height="64" viewBox="0 0 64 64" aria-hidden="true"><path d="M6,28 H58 L52,54 H12 Z" fill="none" stroke="#fff" stroke-width="3" stroke-linejoin="round"/><path d="M14,28 C16,16 48,16 50,28" fill="none" stroke="#fff" stroke-width="3"/><circle cx="32" cy="14" r="3" fill="#fff"/><path d="M10,10 L14,16 M54,10 L50,16" stroke="#fff" stroke-width="3" stroke-linecap="round"/></svg>
    steam
  </div>
  <div class="cook" style="left:617px">
    <svg width="70" height="64" viewBox="0 0 70 64" aria-hidden="true"><rect x="3" y="8" width="64" height="48" rx="3" fill="none" stroke="#fff" stroke-width="3"/><rect x="10" y="15" width="40" height="34" fill="none" stroke="#fff" stroke-width="3"/><circle cx="58" cy="20" r="3" fill="#fff"/><circle cx="58" cy="30" r="3" fill="#fff"/><circle cx="58" cy="40" r="3" fill="#fff"/></svg>
    microwave
  </div>
  <div class="cook" style="left:832px">
    <svg width="70" height="64" viewBox="0 0 70 64" aria-hidden="true"><path d="M24,4 l-3,8 M32,4 l-3,8 M40,4 l-3,8 M48,4 l-3,8" stroke="#fff" stroke-width="2.5" stroke-linecap="round"/><rect x="12" y="22" width="46" height="34" rx="3" fill="none" stroke="#fff" stroke-width="3"/><line x1="4" y1="26" x2="66" y2="26" stroke="#fff" stroke-width="3" stroke-linecap="round"/></svg>
    boil in the bag
  </div>
  <div class="dish" style="left:186px;background:radial-gradient(circle,#d8a866 0 35%,#f1efe9 60%,#1d1d1d 90%)" role="img" aria-label="Oven baked dumpling with chips and peas"></div>
  <div class="dish" style="left:401px;background:radial-gradient(circle,#c98a4a 0 35%,#f1efe9 62%,#1d1d1d 92%)" role="img" aria-label="Steamed dumpling with roasted carrots"></div>
  <div class="dish" style="left:615px;background:radial-gradient(circle,#c7a25c 0 35%,#f1efe9 62%,#1d1d1d 92%)" role="img" aria-label="Microwaved dumpling with potatoes and asparagus"></div>
  <div class="dish" style="left:830px;background:radial-gradient(circle,#d0ac70 0 30%,#7fae4d 42%,#f1efe9 62%,#1d1d1d 92%)" role="img" aria-label="Boil in the bag dumpling with peas and mash"></div>
</section>

<section class="history">
  <h2 class="section-title" style="top:2004px;font-size:36px;color:var(--blue)">WHY ARE THEY CALLED RAG PUDDINGS?</h2>
  <p class="lead" style="left:160px;top:2070px;width:880px;color:var(--blue)">Historically, the puddings take their name from the cloth they are wrapped in while they are steamed. Today, a hi-tech material is used instead of the original `rags’.</p>
</section>

<section class="sweet">
  <h2 class="section-title" style="top:2350px;font-size:48px;color:var(--white)">SWEET OR SAVOURY?</h2>
  <p class="abs sweet-copy">Our rag puddings<br>aren’t just for savoury<br>pallets, we also cater<br>for your sweet tooth!</p>
  <svg class="photo" style="left:505px;top:2540px" width="695" height="545" viewBox="0 0 695 545" role="img" aria-label="Apple cloth dumpling topped with warm custard">
    <defs><linearGradient id="apple" x1="0" y1="0" x2="1" y2="0"><stop offset="0" stop-color="#9a6a33"/><stop offset=".45" stop-color="#c58b45"/><stop offset=".7" stop-color="#f1e08a"/><stop offset="1" stop-color="#f6eaa4"/></linearGradient></defs>
    <path d="M40,130 C80,40 200,0 330,10 C470,20 620,30 695,90 V520 C600,545 420,545 260,520 C120,500 30,460 10,380 C0,290 10,200 40,130 Z" fill="url(#apple)"/>
  </svg>
  <h3 class="abs apple-title">TRY OUR APPLE<br>RAG PUDDINGS !</h3>
  <a href="#" class="btn" style="left:45px;top:3094px;width:188px;height:47px;font-size:22px">GO TO SHOP</a>
</section>

<section class="quality">
  <h2 class="abs" style="right:80px;top:3218px;font-family:var(--head);font-weight:400;font-size:50px;letter-spacing:3px;color:var(--white)">QUALITY MATTERS!</h2>
  <p class="lead" style="right:80px;top:3343px;width:940px;text-align:right;color:var(--white)">Our purpose built facilities are dedicated to providing<br>consistantly perfect rag puddings to customers worldwide</p>
  <div class="factory" style="left:79px;width:246px;background:linear-gradient(135deg,#cfd8e6,#8c9bb3 60%,#4a6aa8)" role="img" aria-label="Bakers preparing dumplings on steel benches"></div>
  <div class="factory" style="left:348px;width:242px;background:linear-gradient(135deg,#d8dde4,#a8b0ba 55%,#6f7a88)" role="img" aria-label="Industrial dough mixers"></div>
  <div class="factory" style="left:613px;width:243px;background:linear-gradient(135deg,#c9d3e2,#8796b0 55%,#2f4f9a)" role="img" aria-label="Staff in protective clothing at the production line"></div>
  <div class="factory" style="left:878px;width:242px;background:linear-gradient(135deg,#3a5ba8,#a0acc0 55%,#dfe3ea)" role="img" aria-label="Worker sealing dumplings by hand"></div>
</section>

<section class="contact">
  <h2 class="section-title" style="top:3838px;font-size:54px;color:var(--blue)">CONTACT US</h2>
  <p class="abs" style="left:0;top:3932px;width:1200px;text-align:center;font-size:22px;letter-spacing:1px">Please contact us via this form and we will get back to you soon</p>
  <form class="contact-form">
    <label>Your Name (required)</label><span class="field"></span>
    <label>Your Email (required)</label><span class="field"></span>
    <label>Subject</label><span class="field"></span>
    <label>Your Message</label><span class="field tall" style="margin-bottom:30px"></span>
    <label class="spam">Spam filter: What is the capital of England?</label><span class="field"></span>
  </form>
  <a href="#" class="btn" style="left:239px;top:4480px;width:105px;height:46px;font-size:22px">SEND</a>
</section>

<footer>
  <div class="footer-col" style="left:49px"><h4>Company</h4><p>Bramwell's Meadow Larder Limited</p></div>
  <div class="footer-col" style="left:416px"><h4>Contact</h4><p>info@meadowlarder.example</p></div>
  <div class="footer-col" style="left:754px"><h4>Legal</h4><a href="#">Terms &amp; Conditions</a><a href="#">Privacy</a><a href="#">Cookies</a></div>
  <div class="footer-col" style="left:1014px"><h4>Follow us</h4>
    <div class="social"><span role="img" aria-label="Social profile one"></span><span role="img" aria-label="Social profile two"></span><span role="img" aria-label="Social profile three"></span></div>
  </div>
  <div class="rule"></div>
  <p class="copyright">© 2019 Bramwell's Cloth Dumplings All rights reserved.</p>
</footer>

</div>
</body>
</html>
```